Family business needs stationery redesign with new logo

Family owned company, established in 1987 wanting a brand 'refresh'. We are an electrical, refrigeration and construction company based in the Barkly Region Northern Territory, Australia. We have a new logo we would like to use which is uploaded along with our current letterhead and email signature. We are also dropping the word 'contractors' so please do not include this on any designs. Please note also, the 'orange' color used in our logo and designs should be Northern Territory red ochre which is as follows:

RGB (Hex): #C75B12
PantoneĀ® 159 C
CMYK: 1 / 74 / 100 / 7

We are needing our stationery redesigned using our new logo. Please include letterheads, business cards, envelopes, and email signatures.

We currently use our business letterheads for quotations, invoices, letters, HR matters, and internal memos.

We also need a separate simplified letterhead for internal paperwork such as employee leave forms, meeting agendas, and meeting minutes etc.

Reason: Needing more submissions of full package designs. We are wanting all our stationery, including business cards, letterheads, email signatures, envelopes, etc to be cohesive. We also require ALL the information, as supplied on our template letterhead, to be included on the new letterhead designs. including electrical license no.etc Thank you, R&W

Reason: needing more time as work has got in the way of looking over designs. A lot of designs not meeting the brief/criteria.

Industry/Entity Type

Business

Colors
0355a3
f37122

Requirements
Must have
• The 'orange' color used in the designs should be Northern Territory red ochre which is as follows:
• RGB (Hex): #C75B12
• PantoneĀ® 159 C
• CMYK: 1 / 74 / 100 / 7
• ***MUST INCLUDE ALL INFORMATION THAT IS ON OUR CURRENT LETTERHEAD***
Should not have
• Please do not include the word 'contractors'

```html
<!DOCTYPE html>
<html lang="en">
<head>
<meta charset="utf-8">
<title>R&amp;W Stationery</title>
<link href="https://fonts.googleapis.com/css2?family=Open+Sans:wght@400;600&display=swap" rel="stylesheet">
<style>
:root{
  --navy:#1b3070;
  --ochre:#e8612a;
  --paper:#ffffff;
  --backdrop:#dfe0df;
  --ink:#3a3a3a;
  --icon:#333333;
}
*{margin:0;padding:0;box-sizing:border-box}
html,body{width:1200px;height:1000px;overflow:hidden}
body{background:var(--backdrop);font-family:'Open Sans',Arial,sans-serif;color:var(--ink);position:relative}
.sheet{position:absolute;background:var(--paper);box-shadow:0 8px 8px -6px rgba(0,0,0,.22);overflow:hidden}
.band{position:absolute;left:0;width:100%;display:block}
.wordmark{position:absolute;color:var(--ochre);font-weight:600;line-height:1;white-space:nowrap;transform:translate(-50%,-50%)}
.contact{position:absolute;font-size:5px;line-height:6.2px;color:#222}
.contact span{display:block;white-space:nowrap}
.contact i{display:inline-block;width:5px;height:5px;border-radius:50%;background:var(--icon);margin-right:2px;vertical-align:-1px}
.contact-row{position:absolute;display:flex;gap:14px;font-size:5px;line-height:8px;color:#222}
.contact-row span{display:block;white-space:nowrap}
.contact-row i{display:inline-block;width:5px;height:5px;border-radius:50%;background:var(--icon);margin-right:3px;vertical-align:-1px}
.contact-row .indent{padding-left:8px}

.card-front{left:75px;top:163px;width:229px;height:130px}
.card-back{left:334px;top:163px;width:228px;height:130px;background:var(--navy)}
.slip{left:55px;top:341px;width:551px;height:240px}
.envelope{left:61px;top:615px;width:551px;height:240px}
.envelope-flap{position:absolute;left:0;top:0;width:100%;height:82px;background:var(--navy);border-radius:0 0 20px 20px}
.letterhead{left:639px;top:137px;width:506px;height:715px}

.letter-body{position:absolute;left:96px;top:165px;width:330px;font-size:11.4px;line-height:14.4px;color:#333}
.letter-body p{text-align:justify;margin-bottom:14.4px}
.letter-body .salutation{margin-bottom:7px}
.signature{font-size:10.5px;line-height:14px;margin-top:-1px}
.signature .name{text-transform:uppercase}
.signature .role{font-size:9px}
</style>
</head>
<body>

<section class="sheet card-front" aria-label="Business card front">
  <div class="wordmark" style="left:56px;top:59px;font-size:19px">R&amp;W</div>
  <div class="contact" style="left:142px;top:66px">
    <span><i></i>42 Ridge ST, Dune Creek</span>
    <span>&nbsp;&nbsp;NT 0870. PO Box 2210</span>
    <span><i></i>08 8150 246</span>
    <span><i></i>0400 5678 910</span>
    <span><i></i>0808150 246</span>
    <span><i></i>info@rwbuild.com.au</span>
    <span><i></i>www.rwbuild.com.au</span>
  </div>
  <svg class="band" style="top:111px;height:10px" viewBox="0 0 229 10" preserveAspectRatio="none">
    <polygon points="0,0 125,0 120,10 0,10" fill="var(--navy)"/>
    <polygon points="125,0 229,0 229,10 120,10" fill="var(--ochre)"/>
  </svg>
</section>

<section class="sheet card-back" aria-label="Business card back">
  <div class="wordmark" style="left:114px;top:65px;font-size:36px">R&amp;W</div>
  <svg class="band" style="top:110px;height:12px" viewBox="0 0 228 12" preserveAspectRatio="none">
    <polygon points="165,0 228,0 228,12 161,12" fill="var(--ochre)"/>
  </svg>
</section>

<section class="sheet slip" aria-label="Compliment slip">
  <div class="wordmark" style="left:58px;top:158px;font-size:22px">R&amp;W</div>
  <div class="contact-row" style="left:30px;top:194px">
    <div><span><i></i>42 Ridge ST, Dune Creek</span><span class="indent">NT 0870. PO Box 2210</span></div>
    <div><span><i></i>08 8150 246</span><span><i></i>0808150 246</span></div>
    <div><span><i></i>info@rwbuild.com.au</span><span><i></i>www.rwbuild.com.au</span></div>
  </div>
  <svg class="band" style="top:215px;height:18px" viewBox="0 0 551 18" preserveAspectRatio="none">
    <polygon points="0,0 382,0 370,18 0,18" fill="var(--navy)"/>
    <polygon points="382,0 551,0 551,18 370,18" fill="var(--ochre)"/>
  </svg>
</section>

<section class="sheet envelope" aria-label="Envelope">
  <div class="envelope-flap"></div>
  <div class="wordmark" style="left:275px;top:44px;font-size:28px">R&amp;W</div>
</section>

<section class="sheet letterhead" aria-label="Letterhead">
  <div class="wordmark" style="left:252px;top:70px;font-size:28px">R&amp;W</div>
  <div class="letter-body">
    <p class="salutation">Dear Sir/Madam</p>
    <p>Lorem ipsum dolor sit amet, mel dicta signiferumque in, duo in summo albucius, vide idque eos id. Eos eu aperiri omittam. Hinc percipit omittantur pri et, in cum minimum vituperata. Dolor libris no sit, eum id porro tritani disputando, usu mutat dolore interesset ad.</p>
    <p>Zril tacimates splendide vim ex, ut falli docendi pro. At ubique pericula mei. Te exerci voluptatum sit, vix at esse ullum scaevola, iusto sonet urbanitas vim ad. No mea ornatus veritus. At est assum fastidii, quo id noluisse phaedrum, mea ea oblique facilisis.</p>
    <p>Sed eu discere delicatissimi, quo probo gloriatur cu, cu est mollis voluptua. No atqui discere saperet quo. Laudem facilisi patrioque ut vim, ut unum aperiam invenire quo, eu sonet veritus corpora qui. Ludus posidonium quo at. Eam ei liber detraxit.</p>
    <p>Ex officiis honestatis usu. Pro regione patrioque similique eu. Animal noluisse et quo, blandit voluptua molestiae eu duo, eos et labore labores. Ea recusabo quaestio suavitate duo.</p>
    <p>Duo alienum efficiantur ea, et sea autem aliquando. Ei eam wisi inani offendit, tibique erroribus voluptatibus in sit. Altera essent latine in cum, eum an doctus dissentias. Te mea latine copiosae percipitur, vix te docendi singulis gloriatur. Ex omnium inermis gloriatur his, impetus tamquam quo an. Ut has aeterno mandamus.</p>
    <div class="signature"><div class="name">John Doe</div><div class="role">President</div></div>
  </div>
  <div class="contact-row" style="left:38px;top:659px">
    <div><span><i></i>42 Ridge ST, Dune Creek</span><span class="indent">NT 0870. PO Box 2210</span></div>
    <div><span><i></i>08 8150 246</span><span><i></i>0808150 246</span></div>
    <div><span><i></i>info@rwbuild.com.au</span><span><i></i>www.rwbuild.com.au</span></div>
  </div>
  <svg class="band" style="top:688px;height:19px" viewBox="0 0 506 19" preserveAspectRatio="none">
    <polygon points="0,0 370,0 363,19 0,19" fill="var(--navy)"/>
    <polygon points="370,0 506,0 506,19 363,19" fill="var(--ochre)"/>
  </svg>
</section>

</body>
</html>
```